Web design for Crowdfunding site HopeWingsRally.com

We need a web design for christian crowdfunding website. Here is the challenge: We need responsive layout that is targeted first in iPad size of screen. It should also scale somehow down to iPhone size of screens. Web layout can be about the same size as iPad screen.

Screens should work so that main page scrolls not but only certain part of the screen scrolls and always one "page" at time. We can implement these "scrolls" then later with javascript but now we need only design. The challenge is to create this kind of hybrid website / app look.

Target is at first to raise funds to orphan people needing about $40 per month for their living and education. There is always some organization which takes care of these kids. Later there will be other christian missions included. At first we are looking to find monthly supporters.

You can be as creative as you want :) As you see from the look and feel sector, I am not looking any same traditional look which many "help kids" sites have. I am looking to reach now younger generation and therefore iPad and mobile are the main screen sizes.

Inspirational designs:
- https://example-gallery.test/profiles/studiofernlake/designs/482716?from=%2Fbrowse%2Fxhr%2Fdesigns%3Fcategory%3Dmobile-app-design
- http://www.artpoolhub.test/design/8261047 Clear, simple visuals
- http://www.artpoolhub.test/design/7394215 Header
- http://www.artpoolhub.test/design/6048392 Contrast in the colors, i think is powerfull

Some terms could be: Kids play, kids are learning (in the school). No static posture but living like kids are. I wonder also how we could also add little bit gaming style even though the question is of reali life of real people. Giving should be rewarding.

Target Market(s)

People who want help other people.

Industry/Entity Type

Christian

Number of Pages Required

4 page

Requirements
Must have
• Homepage. Mission page (In my wireframes it was one kid).
Nice to have
• Other pages and some idea how to scroll. 4 pages is no must. If you feel easy, please give first some draft and I give comments on that.

```html
<!DOCTYPE html>
<html lang="en">
<head>
<meta charset="utf-8">
<title>HopeWings Rally</title>
<link href="https://fonts.googleapis.com/css2?family=Roboto:wght@400;500;700;900&display=swap" rel="stylesheet">
<style>
  :root {
    --brand-yellow: #ffc000;
    --ink: #000000;
    --paper: #ffffff;
    --scene-dark: #2e2a24;
    --scene-mid: #5a5246;
    --scene-warm: #6b5a44;
    --scene-teal: #2f5c5e;
  }
  * { box-sizing: border-box; margin: 0; padding: 0; }
  html, body { width: 1200px; height: 900px; overflow: hidden; }
  body { font-family: "Roboto", Arial, sans-serif; background: var(--scene-dark); }

  .canvas { position: relative; width: 1200px; height: 900px; overflow: hidden; }

  .hero-photo {
    position: absolute; inset: 73px 0 0 0;
    background:
      radial-gradient(ellipse 360px 320px at 930px 700px, var(--scene-teal) 0%, transparent 70%),
      radial-gradient(ellipse 300px 360px at 560px 520px, var(--scene-warm) 0%, transparent 75%),
      linear-gradient(100deg, var(--scene-mid) 0%, var(--scene-dark) 45%, #3a342c 70%, var(--scene-dark) 100%);
  }

  .top-bar {
    position: absolute; top: 0; left: 0; width: 1200px; height: 73px;
    background: var(--brand-yellow);
    display: flex; align-items: center;
  }
  .missions-menu {
    position: absolute; left: 29px; top: 0; height: 73px;
    display: flex; align-items: center; gap: 12px;
    font-weight: 500; font-size: 24px; color: var(--ink); letter-spacing: 0.2px;
  }
  .search-button {
    position: absolute; left: 314px; top: 13px;
    width: 47px; height: 47px; border: 2.5px solid var(--ink); border-radius: 50%;
    display: flex; align-items: center; justify-content: center;
  }
  .site-name {
    position: absolute; left: 0; right: 0; top: 0; height: 73px;
    display: flex; align-items: center; justify-content: center;
    font-weight: 500; font-size: 32px; color: var(--ink); letter-spacing: 0.5px;
    pointer-events: none;
  }
  .btn {
    position: absolute; top: 13px; height: 47px; width: 119px;
    display: flex; align-items: center; justify-content: center;
    font-weight: 500; font-size: 20px; border-radius: 3px;
  }
  .btn-login { left: 920px; background: var(--ink); color: var(--paper); }
  .btn-signup { left: 1050px; border: 2px solid var(--paper); color: var(--paper); }

  .headline, .tagline {
    position: absolute; transform: translate(-50%, -50%) rotate(-36deg);
    text-align: center; white-space: nowrap;
  }
  .headline {
    left: 428px; top: 404px;
    font-weight: 700; font-size: 56px; color: var(--brand-yellow); letter-spacing: 0.5px;
  }
  .tagline {
    left: 504px; top: 482px; width: 880px; white-space: normal;
    font-weight: 500; font-size: 22px; line-height: 1.55; color: var(--paper);
  }

  .supporter-network { position: absolute; left: 0; top: 0; width: 1200px; height: 900px; }
</style>
</head>
<body>
<div class="canvas">
  <div class="hero-photo" role="img" aria-label="Photo of three smiling children standing by a wooden fence in a village, dimmed behind the text"></div>

  <header class="top-bar">
    <div class="missions-menu">
      <svg width="28" height="24" viewBox="0 0 28 24" aria-hidden="true">
        <g fill="var(--ink)">
          <rect x="0" y="1" width="5" height="4"/><rect x="9" y="1" width="19" height="4"/>
          <rect x="0" y="10" width="5" height="4"/><rect x="9" y="10" width="19" height="4"/>
          <rect x="0" y="19" width="5" height="4"/><rect x="9" y="19" width="19" height="4"/>
        </g>
      </svg>
      <span>SEE THE MISSIONS</span>
    </div>
    <div class="search-button" aria-label="Search">
      <svg width="20" height="20" viewBox="0 0 20 20" aria-hidden="true">
        <circle cx="8" cy="8" r="6" fill="none" stroke="var(--ink)" stroke-width="2.6"/>
        <line x1="12.5" y1="12.5" x2="18" y2="18" stroke="var(--ink)" stroke-width="2.8" stroke-linecap="round"/>
      </svg>
    </div>
    <div class="site-name">HOPEWINGS RALLY</div>
    <a class="btn btn-login">LOGIN</a>
    <a class="btn btn-signup">SIGNUP</a>
  </header>

  <h1 class="headline">"She has a name. He has dreams."</h1>
  <p class="tagline">She hopes she would have a furure. He is like you." "1 USD a month will help her and him"</p>

  <svg class="supporter-network" viewBox="0 0 1200 900" aria-label="Network of supporters">
    <defs>
      <clipPath id="avatar-clip"><circle cx="50" cy="50" r="48"/></clipPath>
      <symbol id="avatar-male" viewBox="0 0 100 100">
        <circle cx="50" cy="50" r="48" fill="var(--brand-yellow)"/>
        <g clip-path="url(#avatar-clip)" fill="var(--ink)">
          <ellipse cx="50" cy="40" rx="16" ry="21"/>
          <path d="M14 100 Q16 70 38 64 L50 70 L62 64 Q84 70 86 100 Z"/>
        </g>
        <circle cx="50" cy="50" r="48" fill="none" stroke="var(--paper)" stroke-width="4"/>
      </symbol>
      <symbol id="avatar-female" viewBox="0 0 100 100">
        <circle cx="50" cy="50" r="48" fill="var(--brand-yellow)"/>
        <g clip-path="url(#avatar-clip)" fill="var(--ink)">
          <path d="M31 52 Q27 18 50 16 Q73 18 69 52 Q70 62 77 67 L23 67 Q30 62 31 52 Z"/>
          <path d="M14 100 Q16 72 38 66 L50 72 L62 66 Q84 72 86 100 Z"/>
        </g>
        <circle cx="50" cy="50" r="48" fill="none" stroke="var(--paper)" stroke-width="4"/>
      </symbol>
    </defs>

    <g stroke="var(--paper)" stroke-width="2" stroke-dasharray="6 4" fill="none">
      <line x1="844" y1="457" x2="1031" y2="407"/>
      <line x1="1084" y1="451" x2="1031" y2="504"/>
      <line x1="996" y1="604" x2="1005" y2="639"/>
      <line x1="727" y1="533" x2="656" y2="586"/>
      <line x1="674" y1="645" x2="773" y2="703"/>
      <line x1="896" y1="717" x2="955" y2="703"/>
      <line x1="773" y1="752" x2="689" y2="779"/>
      <line x1="607" y1="694" x2="618" y2="750"/>
    </g>

    <use href="#avatar-male" x="1042" y="332" width="112" height="112"/>
    <use href="#avatar-female" x="736" y="442" width="112" height="112"/>
    <use href="#avatar-female" x="928" y="487" width="112" height="112"/>
    <use href="#avatar-male" x="567" y="585" width="98" height="98"/>
    <use href="#avatar-male" x="778" y="668" width="112" height="112"/>
    <use href="#avatar-female" x="961" y="642" width="112" height="112"/>
    <use href="#avatar-male" x="601" y="752" width="82" height="82"/>
  </svg>
</div>
</body>
</html>
```